K & R Acre Works. Business card design

We need a business card designed for a new business. We have a bulldozer and tractor service. We clear land and make wildlife food plots. We provide disking, bush hogging, and site prep services.
I have attached an image of a business card that I like and would like my business cards to look similar.

Target Market(s)

anyone needing bulldozer and/or tractor services

Industry/Entity Type

Business

Contact Information for Business Card

K & R Acre Works, Operated by 7-T-Ranch
Wade Colton
601-472-3358
wcr4817@fieldmail-example.com

Font styles to use
Sans Serif

Colors

Designer to choose colors to be used in the design.

Requirements
Must have
• image of tractor and bulldozer
• Land Clearing
• Wildlife food plots
• Bush Hogging
• Disking
• Site prep
Nice to have
• i have included a image of a business card that i like. I would like mine to be similar.

```html
<!DOCTYPE html>
<html lang="en">
<head>
<meta charset="utf-8">
<title>K &amp; R Acre Works – Business Card</title>
<link rel="stylesheet" href="https://fonts.googleapis.com/css2?family=Roboto+Condensed:wght@400;700&family=Roboto:wght@400&display=swap">
<style>
  :root {
    --backdrop: #e4e1dc;
    --card-white: #f5f5f3;
    --earth-brown: #6b4117;
    --rust-orange: #c27a2e;
    --field-olive: #8e9a3c;
    --ink-dark: #2b2b2b;
    --text-light: #ffffff;
    --photo-dirt: #8a7a55;
    --photo-green: #5f7a3a;
    --photo-sky: #c9d3b8;
  }
  * { margin: 0; padding: 0; box-sizing: border-box; }
  html, body {
    width: 1200px; height: 771px; overflow: hidden;
    background: var(--backdrop);
  }
  .business-card {
    position: absolute; left: 75px; top: 86px;
    width: 1050px; height: 598px;
    border-radius: 30px; overflow: hidden;
    background: var(--card-white);
    box-shadow: 0 6px 18px rgba(0,0,0,0.18);
  }
  .card-shapes { position: absolute; left: 0; top: 0; }
  .brand-name {
    position: absolute; right: 61px; top: 46px;
    font: 700 38px/1 "Roboto Condensed", sans-serif;
    color: var(--earth-brown); letter-spacing: 0.5px;
  }
  .brand-tagline {
    position: absolute; right: 61px; top: 107px;
    font: 700 18px/1 "Roboto Condensed", sans-serif;
    color: var(--ink-dark); letter-spacing: 0.3px;
  }
  .service-photo {
    position: absolute; top: 140px; height: 156px;
    border: 3px solid var(--earth-brown);
  }
  .service-photo.bulldozer {
    left: 508px; width: 257px;
    background: linear-gradient(180deg, var(--photo-sky) 0%, var(--photo-green) 40%, #c9a83a 58%, var(--photo-dirt) 100%);
  }
  .service-photo.tractor {
    left: 779px; width: 206px;
    background: linear-gradient(180deg, var(--photo-green) 0%, #c25a2a 55%, #a58a52 100%);
  }
  .owner-name {
    position: absolute; left: 54px; top: 352px;
    font: 700 35px/1 "Roboto Condensed", sans-serif;
    color: var(--text-light);
  }
  .owner-title {
    position: absolute; left: 56px; top: 391px;
    font: 400 24px/1 "Roboto Condensed", sans-serif;
    color: var(--text-light); letter-spacing: 0.5px;
  }
  .divider {
    position: absolute; left: 54px; top: 443px;
    width: 935px; height: 1px; background: rgba(255,255,255,0.75);
  }
  .contact-list, .service-list {
    position: absolute; top: 472px; list-style: none;
    font: 400 24px/31.5px "Roboto", sans-serif;
    color: var(--text-light);
  }
  .contact-list { left: 58px; }
  .contact-list li { display: flex; align-items: center; gap: 9px; }
  .contact-list svg { width: 20px; height: 20px; flex: none; }
  .service-list { right: 61px; text-align: right; }
  .dot { font-size: 20px; padding: 0 3px; }
</style>
</head>
<body>
  <article class="business-card">
    <svg class="card-shapes" width="1050" height="598" viewBox="0 0 1050 598" aria-hidden="true">
      <path d="M370 364 H1050 V373 H378 Z" fill="var(--rust-orange)"/>
      <path d="M392 380 H1050 V389 H402 Z" fill="var(--field-olive)"/>
      <path d="M0 326 H362 C392 326 396 396 440 396 H1050 V598 H0 Z" fill="var(--earth-brown)"/>
    </svg>

    <h1 class="brand-name">K &amp; R ACRE WORKS</h1>
    <p class="brand-tagline">FOR ALL OF YOUR LAND IMPROVEMENT NEEDS</p>

    <div class="service-photo bulldozer" role="img" aria-label="Photo of a yellow bulldozer clearing land"></div>
    <div class="service-photo tractor" role="img" aria-label="Photo of an orange tractor with a front attachment in a field"></div>

    <h2 class="owner-name">WADE COLTON</h2>
    <p class="owner-title">OWNER</p>
    <div class="divider"></div>

    <ul class="contact-list">
      <li>
        <svg viewBox="0 0 24 24"><path fill="#fff" d="M6.6 10.8a15.1 15.1 0 0 0 6.6 6.6l2.2-2.2a1 1 0 0 1 1-.25 11.4 11.4 0 0 0 3.6.57 1 1 0 0 1 1 1V20a1 1 0 0 1-1 1A17 17 0 0 1 3 4a1 1 0 0 1 1-1h3.5a1 1 0 0 1 1 1c0 1.25.2 2.45.57 3.57a1 1 0 0 1-.25 1z"/></svg>
        601-472-3358
      </li>
      <li>
        <svg viewBox="0 0 24 24"><rect x="2" y="5" width="20" height="14" fill="#fff"/><path d="M2 5 L12 13 L22 5" fill="none" stroke="var(--earth-brown)" stroke-width="2"/></svg>
        wcr4817@fieldmail-example.com
      </li>
      <li>
        <svg viewBox="0 0 24 24"><circle cx="12" cy="12" r="10" fill="#fff"/><path d="M2 12h20M12 2c3 3 3 17 0 20M12 2c-3 3-3 17 0 20" fill="none" stroke="var(--earth-brown)" stroke-width="1.5"/></svg>
        acreworks-example.com
      </li>
    </ul>

    <ul class="service-list">
      <li>Land Clearing</li>
      <li>Wildlife food plots<span class="dot">•</span>Disking</li>
      <li>Bush Hogging<span class="dot">•</span>Site prep</li>
    </ul>
  </article>
</body>
</html>
```